Zelvo Stationary

Design the stationary of Zelvo Promotions Group.

Zelvo is a BTL company, BTL meaning "below the line". In other words Zelvo is a Promotional Marketing company (the company that design the brands promotional activities).

The design should transmit creativity, agility, boldness.

I need:
* Bis Card
* Letter head
* Envelopes, both vertical and horizontal (for legal size), and letter envelope
* Folders
* PPT template (Title page and regular page)
* CD slip (CD envelope)
* ID card (employee card)

And what ever else you want to throw in.
Updates

Guys,

Something I missed from the brief.   The predominat color should be RED.

Also, have fun and play with the exclamation mark (!) of the logo. 

Hi guys, more comments:

Remember that Zelvo is a "creativity" agency, not in the advertising side but on the promotional side, and that should reflect on the stationary.

 I want a bold design.  Bold and yet crisp.

 

Guys, i just uploaded the Logo in AI format.

I Also uploaded the actual Zelvo Bis Card, wich I like.  So I will like to see some designs with that bis card approach.

Guys, I am so sorry, but I notice in your last post that I upladed a wrong design ("13154_promotions_group_zelvo_brief225630.ai").  The problem was that I asked the designer the file in AI format and he send me thw wrong file, and since I dont have Illustrator I could not verify it.

The differences are minor, I just already ask him the correct one (similar to the EPS file).

Sorry                                   

Just post the correct AI file : "Zelvo Logo.ai"

Reason: I'm expecting more designs to choose from and also I wont be available tomorrow to decide.

Reason: Sorry guys, but we are not there yet!

Target Market(s)

Marketing directors, Marketing Managers

Industry/Entity Type

Legal

Requirements
Must have
• Must work with the logo attached.
The predominat color should be RED.
Play and have fun with the exclamation mark (!).
Should not have
• * No old fonts

Should not be:
* boring
* Informal
* rigid

```html
<!DOCTYPE html>
<html lang="en">
<head>
<meta charset="utf-8">
<title>Zelvo Promotions Group – Letterhead Options</title>
<link rel="stylesheet" href="https://fonts.googleapis.com/css2?family=Ubuntu:wght@400;700&family=Open+Sans:wght@400;700&display=swap">
<style>
  :root {
    --red: #d7262e;
    --red-motif: rgba(215, 38, 46, 0.30);
    --red-fade: rgba(215, 38, 46, 0);
    --grey-motif: rgba(120, 120, 120, 0.22);
    --ink: #2b2b2b;
    --grey: #8a8a8a;
    --footer: #ececec;
    --paper: #ffffff;
    --backdrop: #4a4a4a;
    --label: #f2f2f2;
  }
  * { box-sizing: border-box; margin: 0; padding: 0; }
  html, body { width: 1200px; height: 581px; overflow: hidden; }
  body {
    background: var(--backdrop);
    font-family: "Open Sans", Arial, sans-serif;
    color: var(--ink);
    position: relative;
  }

  .sheet {
    position: absolute;
    top: 74px;
    width: 332px;
    height: 437px;
    background: var(--paper);
    overflow: hidden;
    box-shadow: 0 4px 14px rgba(0, 0, 0, 0.45);
  }
  .sheet--one { left: 76px; }
  .sheet--two { left: 431px; }
  .sheet--three { left: 776px; }

  .top-band { position: absolute; top: 0; left: 0; right: 0; height: 5px; background: var(--red); }

  /* large brand motif area, kept as a soft tonal field */
  .motif { position: absolute; z-index: 0; }
  .sheet--one .motif {
    left: 0; top: 190px; width: 130px; height: 247px;
    background: radial-gradient(ellipse at 30% 60%, var(--red-motif), var(--grey-motif) 55%, var(--red-fade) 80%);
  }
  .sheet--two .motif {
    right: 0; top: 60px; width: 110px; height: 340px;
    background: radial-gradient(ellipse at 70% 55%, var(--grey-motif), var(--red-motif) 50%, var(--red-fade) 78%);
  }
  .sheet--three .motif {
    left: 110px; top: 135px; width: 130px; height: 200px;
    background: radial-gradient(ellipse at 50% 50%, var(--red-motif), var(--grey-motif) 50%, var(--red-fade) 78%);
  }

  .brand { position: absolute; z-index: 1; top: 14px; left: 22px; display: flex; align-items: flex-start; gap: 6px; }
  .brand-name { font-family: "Ubuntu", Arial, sans-serif; font-weight: 700; font-size: 27px; line-height: 1; color: var(--ink); }
  .brand-sub { font-family: "Ubuntu", Arial, sans-serif; font-weight: 700; font-size: 5.5px; color: var(--ink); letter-spacing: 0.8px; margin-top: 2px; }
  .brand-dot { width: 18px; height: 18px; border-radius: 50%; background: var(--red); margin-top: 3px; }

  .contact { position: absolute; z-index: 1; top: 18px; right: 22px; font-style: normal; font-size: 5px; line-height: 1.6; color: var(--grey); }
  .contact p { display: flex; align-items: center; gap: 2px; }
  .contact svg { width: 4px; height: 4px; fill: var(--red); }

  .letter { position: absolute; z-index: 1; top: 100px; left: 22px; right: 22px; font-size: 5.8px; line-height: 1.55; }
  .letter p { margin-bottom: 11px; }
  .letter .salutation { font-weight: 700; margin-bottom: 6px; }
  .letter .list-title { margin-bottom: 4px; }
  .letter ul { margin: 0 0 14px 10px; list-style: none; }
  .letter li { font-weight: 700; }
  .letter li::before { content: "•"; color: var(--red); margin-right: 3px; }
  .signature { width: 62px; height: 16px; margin: 2px 0 6px; background: linear-gradient(90deg, rgba(43,43,43,0.35), rgba(43,43,43,0.08)); border-radius: 8px; }
  .signer { font-size: 5.2px; color: var(--grey); }

  .footer-band { position: absolute; z-index: 1; left: 0; right: 0; bottom: 0; height: 34px; background: var(--footer); font-size: 5px; color: var(--grey); padding: 9px 22px; line-height: 1.6; }
  .footer-band b { color: var(--red); }

  .option-label { position: absolute; top: 520px; width: 332px; text-align: center; font-family: "Ubuntu", Arial, sans-serif; font-weight: 700; font-size: 30px; color: var(--label); }
</style>
</head>
<body>

<section class="sheet sheet--one">
  <div class="top-band"></div>
  <div class="motif" role="img" aria-label="large faint brand motif in red and grey"></div>
  <header class="brand">
    <div><div class="brand-name">zelvo</div><div class="brand-sub">PROMOTIONS GROUP</div></div>
    <span class="brand-dot"></span>
  </header>
  <address class="contact">
    <p>P.O. Box 4820 Marlow, 2760 North Bay</p>
    <p><svg viewBox="0 0 4 4"><circle cx="2" cy="2" r="2"/></svg>+000 (2) 555 0142</p>
    <p><svg viewBox="0 0 4 4"><circle cx="2" cy="2" r="2"/></svg>+000 (2) 555 0143</p>
    <p>www.zelvo.com</p>
  </address>
  <article class="letter">
    <p class="salutation">Dear Mr. First Last</p>
    <p>An overview of our approach to promotional work follows here, with a short note on timing, budget and the activities we propose for the coming season. Our team builds field events, sampling days and retail displays that put the brand in front of buyers at the very moment they decide. We plan each step with care, brief every promoter in person and report results in clear terms, so your managers can act quickly on what works best. Each activity is measured against the goals we agree at the start, and we adjust the plan as the numbers come in. This keeps the budget lean and the message sharp across every store, street and stand where your customers meet the brand.</p>
    <p class="list-title">Qualifications:</p>
    <ul><li>field event planning</li><li>retail display design</li><li>sampling team staffing</li></ul>
    <p>Please review the attached proposal and let us know a good time to meet. We would be glad to walk you through each idea in person, show samples of recent work and shape the plan around your goals for the coming quarter. Our studio can also prepare mock-ups of displays and promoter kits before the first meeting, so your team sees the full picture early and can give feedback while there is still time to refine every detail.</p>
    <p>Sincerely,</p>
    <div class="signature" role="img" aria-label="handwritten signature"></div>
    <p class="signer">Dana Keller</p>
  </article>
</section>

<section class="sheet sheet--two">
  <div class="motif" role="img" aria-label="large faint brand motif in grey and red"></div>
  <header class="brand">
    <div><div class="brand-name">zelvo</div><div class="brand-sub">PROMOTIONS GROUP</div></div>
    <span class="brand-dot"></span>
  </header>
  <article class="letter">
    <p class="salutation">Dear Mr. First Last</p>
    <p>An overview of our approach to promotional work follows here, with a short note on timing, budget and the activities we propose for the coming season. Our team builds field events, sampling days and retail displays that put the brand in front of buyers at the very moment they decide. We plan each step with care, brief every promoter in person and report results in clear terms, so your managers can act quickly on what works best. Each activity is measured against the goals we agree at the start, and we adjust the plan as the numbers come in. This keeps the budget lean and the message sharp across every store, street and stand where your customers meet the brand.</p>
    <p class="list-title">Qualifications:</p>
    <ul><li>field event planning</li><li>retail display design</li><li>sampling team staffing</li></ul>
    <p>Please review the attached proposal and let us know a good time to meet. We would be glad to walk you through each idea in person, show samples of recent work and shape the plan around your goals for the coming quarter. Our studio can also prepare mock-ups of displays and promoter kits before the first meeting, so your team sees the full picture early and can give feedback while there is still time to refine every detail.</p>
    <p>Sincerely,</p>
    <div class="signature" role="img" aria-label="handwritten signature"></div>
    <p class="signer">Dana Keller</p>
  </article>
  <footer class="footer-band">
    <p>P.O. Box 4820 Marlow, 2760 North Bay</p>
    <p><b>t</b> +000 (2) 555 0142 &nbsp; <b>f</b> +000 (2) 555 0143 &nbsp; www.zelvo.com</p>
  </footer>
</section>

<section class="sheet sheet--three">
  <div class="motif" role="img" aria-label="large faint brand motif in red and grey"></div>
  <header class="brand">
    <div><div class="brand-name">zelvo</div><div class="brand-sub">PROMOTIONS GROUP</div></div>
    <span class="brand-dot"></span>
  </header>
  <address class="contact">
    <p>P.O. Box 4820 Marlow, 2760 North Bay</p>
    <p><svg viewBox="0 0 4 4"><circle cx="2" cy="2" r="2"/></svg>+000 (2) 555 0142</p>
    <p><svg viewBox="0 0 4 4"><circle cx="2" cy="2" r="2"/></svg>+000 (2) 555 0143</p>
    <p>www.zelvo.com</p>
  </address>
  <article class="letter">
    <p class="salutation">Dear Mr. First Last</p>
    <p>An overview of our approach to promotional work follows here, with a short note on timing, budget and the activities we propose for the coming season. Our team builds field events, sampling days and retail displays that put the brand in front of buyers at the very moment they decide. We plan each step with care, brief every promoter in person and report results in clear terms, so your managers can act quickly on what works best. Each activity is measured against the goals we agree at the start, and we adjust the plan as the numbers come in. This keeps the budget lean and the message sharp across every store, street and stand where your customers meet the brand.</p>
    <p class="list-title">Qualifications:</p>
    <ul><li>field event planning</li><li>retail display design</li><li>sampling team staffing</li></ul>
    <p>Please review the attached proposal and let us know a good time to meet. We would be glad to walk you through each idea in person, show samples of recent work and shape the plan around your goals for the coming quarter. Our studio can also prepare mock-ups of displays and promoter kits before the first meeting, so your team sees the full picture early and can give feedback while there is still time to refine every detail.</p>
    <p>Sincerely,</p>
    <div class="signature" role="img" aria-label="handwritten signature"></div>
    <p class="signer">Dana Keller</p>
  </article>
</section>

<div class="option-label" style="left:76px">1</div>
<div class="option-label" style="left:431px">2</div>
<div class="option-label" style="left:776px">3</div>

</body>
</html>
```